Corvane Paintless Dent Removal

Our company works on vehicles removing dents using a highly skilled trade which the metal is massaged out with special tools without disturbing the original paint, hence paintless dent removal. Besides keeping the paint and metal original its also very environmentally friendly since no paint or toxic fillers are used. Also we we are one of the most experienced companies in the business with 25 years

Target Market(s)

Retail Automobile consumers, Auto Dealerships and Auto Body Shops

Industry/Entity Type

Auto Repair

Contact Information for Business Card

Dale Hollister
PO Box 518 Brookmere, NY 11962
631-555-0148
corvanepdr@mailbox-example.com
website corvanepdr.example
youtube corvane paintless dent removal
25 years of experience removing Dents, Dings and Hail Damage

Font styles to use
Serif
Sans Serif

Colors

Designer to choose colors to be used in the design.

Requirements
Must have
• I do like things that are simple but classy and somewhat bold, also I like my logo so that should be somewhat important

```html
<!DOCTYPE html>
<html lang="en">
<head>
<meta charset="utf-8">
<title>Corvane Paintless Dent Removal – Business Card</title>
<link rel="stylesheet" href="https://fonts.googleapis.com/css2?family=Open+Sans:wght@400;600;700;800&display=swap">
<style>
  :root {
    --navy: #13224a;
    --green: #5cb83a;
    --white: #ffffff;
    --paper: #f7f8f8;
    --ink: #4a4d52;
    --stage: #e9e7e3;
  }
  * { box-sizing: border-box; margin: 0; padding: 0; }
  html, body { width: 1200px; height: 800px; overflow: hidden; }
  body {
    background: var(--stage);
    font-family: "Open Sans", Verdana, sans-serif;
    display: flex;
    align-items: center;
    justify-content: center;
    gap: 60px;
  }
  .card {
    position: relative;
    width: 525px;
    height: 300px;
    box-shadow: 0 6px 18px rgba(0,0,0,.15);
    overflow: hidden;
  }

  /* Back */
  .card-back { background: var(--navy); color: var(--white); }
  .card-back .brand-name {
    position: absolute;
    left: 0; right: 0; top: 92px;
    text-align: center;
    font-weight: 800;
    font-size: 34px;
    line-height: 1.05;
    text-transform: uppercase;
    letter-spacing: .5px;
    color: var(--white);
  }
  .card-back .brand-name small {
    display: block;
    font-size: 17px;
    text-transform: none;
    letter-spacing: 0;
  }
  .channel {
    position: absolute;
    left: 0; right: 0; bottom: 34px;
    display: flex;
    justify-content: center;
    align-items: center;
    gap: 9px;
    font-size: 13px;
  }
  .channel .mark { width: 14px; height: 11px; background: var(--white); border-radius: 2px; }

  /* Front */
  .card-front { background: var(--paper); color: var(--ink); }
  .card-front .band {
    position: absolute; left: 0; right: 0; bottom: 0; height: 26px;
    background: var(--navy);
  }
  .person { position: absolute; left: 34px; top: 60px; }
  .person .name {
    font-weight: 800; font-size: 17px; letter-spacing: .6px;
    text-transform: uppercase; color: var(--navy);
  }
  .person .name .last { color: var(--green); }
  .person .role { font-size: 11px; letter-spacing: .6px; margin-top: 1px; }
  .address { position: absolute; left: 34px; top: 122px; font-size: 12.5px; line-height: 1.35; }
  .contacts { position: absolute; left: 34px; top: 178px; list-style: none; font-size: 12.5px; line-height: 1.3; }
  .contacts li { display: flex; align-items: center; gap: 8px; }
  .contacts svg { width: 11px; height: 11px; fill: var(--green); flex: none; }
  .card-front .brand-name {
    position: absolute; right: 38px; top: 66px; width: 220px;
    text-align: center;
    font-weight: 800; font-size: 30px; line-height: 1.05;
    text-transform: uppercase; color: var(--navy);
  }
  .card-front .brand-name small { display: block; font-size: 15px; text-transform: none; }
  .tagline {
    position: absolute; right: 34px; bottom: 40px;
    text-align: right; font-size: 12.5px; line-height: 1.3;
  }
</style>
</head>
<body>

  <section class="card card-back" aria-label="Card back">
    <div class="brand-name">Corvane<small>Paintless Dent Removal</small></div>
    <div class="channel"><span class="mark"></span><span>Corvane Paintless Dent Removal</span></div>
  </section>

  <section class="card card-front" aria-label="Card front">
    <div class="person">
      <div class="name">Dale <span class="last">Hollister</span></div>
      <div class="role">OWNER</div>
    </div>
    <div class="address">PO Box 518 Brookmere<br>NY 11962</div>
    <ul class="contacts">
      <li><svg viewBox="0 0 24 24"><path d="M6.6 10.8a15 15 0 0 0 6.6 6.6l2.2-2.2a1 1 0 0 1 1-.25 11.4 11.4 0 0 0 3.6.57 1 1 0 0 1 1 1V20a1 1 0 0 1-1 1A17 17 0 0 1 3 4a1 1 0 0 1 1-1h3.5a1 1 0 0 1 1 1c0 1.25.2 2.45.57 3.57a1 1 0 0 1-.25 1z"/></svg>631-555-0148</li>
      <li><svg viewBox="0 0 24 24"><path d="M2 5h20v14H2z M2 5l10 8 10-8" fill="var(--green)"/><path d="M3 6l9 7 9-7" stroke="#fff" stroke-width="1.6" fill="none"/></svg>corvanepdr@mailbox-example.com</li>
      <li><svg viewBox="0 0 24 24"><circle cx="12" cy="12" r="10"/><path d="M2 12h20M12 2c3 3 3 17 0 20M12 2c-3 3-3 17 0 20" stroke="#fff" stroke-width="1.4" fill="none"/></svg>www.corvanepdr.example</li>
    </ul>
    <div class="brand-name">Corvane<small>Paintless Dent Removal</small></div>
    <p class="tagline">25 years of experience removing<br>Dents, Dings and Hail Damage</p>
    <div class="band"></div>
  </section>

</body>
</html>
```